Working Capital graphics

Our business advisory firm requires 9 images to be re-created and improved in the branding of our business.

The 9 images have been uploaded below and the colours and branding of the business can be found at the website www.tallowmereadvisory.com.au

```html
<!DOCTYPE html>
<html lang="en">
<head>
<meta charset="UTF-8">
<title>Inventories – Inventory Drivers</title>
<link href="https://fonts.googleapis.com/css2?family=Roboto:ital,wght@0,500;0,700;1,700&display=swap" rel="stylesheet">
<style>
  :root {
    --brand-blue: #1a56b8;
    --accent-orange: #f7921e;
    --planning-navy: #0a2147;
    --procurement-blue: #0f3580;
    --fulfillment-blue: #2079d4;
    --product-teal: #1f879d;
    --badge-cyan: #29a9e0;
    --connector: #000000;
    --white: #ffffff;
  }
  * { margin: 0; padding: 0; box-sizing: border-box; }
  html, body { width: 1200px; height: 1000px; overflow: hidden; background: var(--white); }
  body { font-family: 'Roboto', Arial, sans-serif; }
  .canvas { position: relative; width: 1200px; height: 1000px; }
  .connectors { position: absolute; inset: 0; }
  .connectors path { fill: none; stroke: var(--connector); stroke-width: 2; }

  .page-title {
    position: absolute; left: 41px; top: 40px;
    font-size: 32px; font-weight: 700; font-style: italic;
    color: var(--brand-blue);
  }
  .column-heading {
    position: absolute; top: 52px; transform: translateX(-50%);
    font-size: 19px; font-weight: 500; color: var(--brand-blue); white-space: nowrap;
  }
  .column-heading.driver { left: 507px; }
  .column-heading.sub { left: 882px; }

  .root-node {
    position: absolute; left: 41px; top: 457px; width: 196px; height: 112px;
    background: var(--accent-orange); color: var(--white);
    display: flex; align-items: center; justify-content: center; text-align: center;
    font-size: 19px; font-weight: 700; line-height: 1.2;
  }

  .driver-bar, .sub-box {
    position: absolute; display: flex; align-items: center; justify-content: center;
    color: var(--white); font-weight: 700; font-style: italic; white-space: nowrap;
  }
  .driver-bar { left: 413px; width: 187px; height: 42px; font-size: 20px; padding-left: 0; }
  .driver-bar span { position: absolute; left: 94px; transform: translateX(-50%); }
  .sub-box { left: 694px; width: 373px; height: 43px; font-size: 20px; }

  .badge {
    position: absolute; width: 62px; height: 62px; border-radius: 50%;
    background: var(--badge-cyan); color: var(--white);
    display: flex; align-items: center; justify-content: center;
    font-size: 30px; font-weight: 700; font-style: italic; left: 362px;
  }

  .planning { background: var(--planning-navy); }
  .procurement { background: var(--procurement-blue); }
  .fulfillment { background: var(--fulfillment-blue); }
  .product { background: var(--product-teal); }
</style>
</head>
<body>
<div class="canvas">
  <svg class="connectors" width="1200" height="1000" viewBox="0 0 1200 1000" aria-hidden="true">
    <path d="M237 513 H303"/>
    <path d="M303 219 V830"/>
    <path d="M303 219 H370 M303 446 H370 M303 637 H370 M303 830 H370"/>
    <path d="M600 217 H648 M648 119 V313 M648 119 H694 M648 185 H694 M648 249 H694 M648 313 H694"/>
    <path d="M600 446 H694 M647 383 V507 M647 383 H694 M647 507 H694"/>
    <path d="M600 639 H694 M647 575 V699 M647 575 H694 M647 699 H694"/>
    <path d="M600 831 H694 M647 768 V892 M647 768 H694 M647 892 H694"/>
  </svg>

  <h1 class="page-title">Inventories</h1>
  <div class="column-heading driver">Driver Group</div>
  <div class="column-heading sub">Sub-group</div>

  <div class="root-node">Inventory<br>Drivers</div>

  <div class="driver-bar planning" style="top:196px"><span>Planning</span></div>
  <div class="badge" style="top:186px">10</div>
  <div class="driver-bar procurement" style="top:425px"><span>Procurement</span></div>
  <div class="badge" style="top:415px">11</div>
  <div class="driver-bar fulfillment" style="top:616px"><span>Fulfillment</span></div>
  <div class="badge" style="top:606px">12</div>
  <div class="driver-bar product" style="top:809px"><span>Product range</span></div>
  <div class="badge" style="top:799px">13</div>

  <div class="sub-box planning" style="top:99px">Demand variability</div>
  <div class="sub-box planning" style="top:165px">Planning collaboration</div>
  <div class="sub-box planning" style="top:229px">Information availability</div>
  <div class="sub-box planning" style="top:293px">Inventory target setting</div>

  <div class="sub-box procurement" style="top:361px">Order quantities</div>
  <div class="sub-box procurement" style="top:424px">Supplier lead time variability</div>
  <div class="sub-box procurement" style="top:485px">Supplier quality variability</div>

  <div class="sub-box fulfillment" style="top:553px">Customer service levels</div>
  <div class="sub-box fulfillment" style="top:617px">Network structure</div>
  <div class="sub-box fulfillment" style="top:678px">Inventory postponement</div>

  <div class="sub-box product" style="top:746px">Customer inventory needs</div>
  <div class="sub-box product" style="top:809px">Part standardisation</div>
  <div class="sub-box product" style="top:871px">SKU proliferation</div>
</div>
</body>
</html>
```